Create a business promotion flyer to leave in customer mailboxes. We are a bulk petroleum supplier, servicing any industry that requires diesel. Base in griffith NSW, servicing griffith area and surrounds.

Business Name - Terra Diesel
Fuel@terradiesel-example.com.au
Owen - 0491 570 362 ohartley@terradiesel-example.com.au
Liam - 0491 570 718 lprosser@terradiesel-example.com.au
Simon - 0491 570 905 skenway@terradiesel-example.com.au
Office 02 5550 1734

Bulk Fuel deliveries.
Oils & lubricants
Local Family owned business

```html
<!DOCTYPE html>
<html lang="en">
<head>
<meta charset="utf-8">
<title>Terra Diesel – Bulk Fuel Flyer</title>
<link href="https://fonts.googleapis.com/css2?family=Barlow+Semi+Condensed:wght@500;600;700&family=Inter:wght@400;500&family=Allura&display=swap" rel="stylesheet">
<style>
  :root{
    --ink:#151515;
    --charcoal:#3b3b3b;
    --red:#d42a26;
    --paper:#ece4da;
    --earth:#3d2714;
    --white:#ffffff;
    --rule:#8c8780;
  }
  *{margin:0;padding:0;box-sizing:border-box}
  html,body{width:800px;height:1200px;overflow:hidden;background:var(--paper)}
  .flyer{position:relative;width:800px;height:1200px;overflow:hidden;background:var(--paper);
    font-family:"Inter",Arial,sans-serif;color:var(--ink)}
  .hero-photo{position:absolute;left:0;top:0;width:800px;height:1000px;
    background:linear-gradient(180deg,#ede5da 0%,#e9ded0 28%,#ecd9c0 48%,#efc996 58%,#e6b27a 63%,#8f6e4c 67%,#765638 78%,#5b4128 100%)}
  .brand{position:absolute;left:62px;top:100px;width:280px;display:flex;align-items:center;gap:12px;
    font-family:"Barlow Semi Condensed",sans-serif;font-weight:700;font-size:44px;color:var(--charcoal);white-space:nowrap}
  .brand-mark{width:22px;height:22px;background:var(--red);flex:none}
  .header-divider{position:absolute;left:365px;top:44px;width:1px;height:196px;background:var(--rule)}
  .headline{position:absolute;left:404px;top:40px;font-family:"Barlow Semi Condensed",sans-serif;
    font-weight:700;font-size:46px;line-height:43.5px;text-transform:uppercase;letter-spacing:-0.3px}
  .headline .accent{color:var(--red)}
  .tagline{position:absolute;left:405px;top:225px;font-family:"Barlow Semi Condensed",sans-serif;
    font-weight:600;font-size:16px;letter-spacing:0.2px}
  .intro{position:absolute;left:0;top:268px;width:800px;text-align:center;font-size:16px;line-height:24px}
  .services{position:absolute;left:86px;top:346px;width:624px;display:grid;grid-template-columns:repeat(3,1fr)}
  .service{text-align:center;height:200px;padding-top:2px;border-left:1px solid var(--rule)}
  .service:first-child{border-left:none}
  .service svg{width:48px;height:52px;stroke:var(--ink);fill:none;stroke-width:2;stroke-linejoin:round;stroke-linecap:round}
  .service h3{font-family:"Barlow Semi Condensed",sans-serif;font-weight:700;font-size:17.5px;line-height:20.5px;margin-top:12px}
  .service p{font-size:13px;line-height:19.5px;margin:10px auto 0;width:140px}
  .region-band{position:absolute;left:0;top:850px;width:800px;height:150px}
  .region-text{position:absolute;left:79px;top:860px;color:var(--white)}
  .region-text h2{font-family:"Barlow Semi Condensed",sans-serif;font-weight:700;font-size:28px;line-height:33px}
  .region-text p{font-size:16px;line-height:25px;margin-top:10px}
  .community{position:absolute;left:485px;top:838px;color:var(--white)}
  .community .script{font-family:"Allura",cursive;font-size:46px;line-height:54px}
  .community .slogan{font-family:"Barlow Semi Condensed",sans-serif;font-weight:700;font-size:18px;margin-top:4px}
  .contacts{position:absolute;left:48px;top:1032px;width:712px;display:grid;grid-template-columns:repeat(4,1fr)}
  .contact{padding:0 0 0 10px;border-left:1px solid var(--rule);height:70px}
  .contact:first-child{border-left:none;padding-left:8px}
  .contact h4{display:flex;align-items:center;gap:10px;font-family:"Barlow Semi Condensed",sans-serif;font-weight:600;font-size:18px}
  .contact h4 svg{width:18px;height:18px;fill:#6b6661}
  .contact .phone{font-size:15px;margin-top:7px}
  .contact .email{font-size:9.6px;margin-top:6px;letter-spacing:-0.1px;white-space:nowrap}
  .footer-rule{position:absolute;left:50px;top:1122px;width:700px;height:1px;background:#55514c}
  .values{position:absolute;left:50px;top:1142px;width:710px;display:grid;grid-template-columns:repeat(4,1fr)}
  .value{display:flex;align-items:center;gap:12px;padding-left:6px;border-left:1px solid var(--rule);height:36px}
  .value:first-child{border-left:none}
  .value svg{width:32px;height:36px;fill:none;stroke:var(--ink);stroke-width:2;stroke-linejoin:round;stroke-linecap:round;flex:none}
  .value strong{display:block;font-family:"Barlow Semi Condensed",sans-serif;font-weight:700;font-size:14px}
  .value span{font-size:10.5px}
</style>
</head>
<body>
<main class="flyer">
  <div class="hero-photo" role="img" aria-label="Photograph of a white road-train fuel tanker on a dirt track beside grain silos under a sunset sky"></div>

  <div class="brand"><span class="brand-mark"></span>Terra Diesel</div>
  <div class="header-divider"></div>
  <h1 class="headline">Fueling<br>Our Region<br><span class="accent">Powering<br>Your Business</span></h1>
  <p class="tagline">RELIABLE. LOCAL. READY TO DELIVER.</p>

  <p class="intro">Proudly supplying high-quality bulk fuel<br>and lubricants to the Griffith area and surrounds.</p>

  <section class="services">
    <div class="service">
      <svg viewBox="0 0 48 52"><rect x="5" y="4" width="24" height="42" rx="3"/><rect x="10" y="10" width="13" height="9" rx="1"/><path d="M2 47h32M29 18h6l4 6v16a3 3 0 0 0 6 0V16l-5-6"/></svg>
      <h3>BULK FUEL<br>DELIVERIES</h3>
      <p>Reliable on-time deliveries of premium diesel.</p>
    </div>
    <div class="service">
      <svg viewBox="0 0 48 52"><path d="M24 4C18 16 9 24 9 34a15 15 0 0 0 30 0C39 24 30 16 24 4z"/><path d="M17 34a7 7 0 0 0 7 7"/></svg>
      <h3>OILS &amp;<br>LUBRICANTS</h3>
      <p>Quality products to keep your equipment performing.</p>
    </div>
    <div class="service">
      <svg viewBox="0 0 56 52" style="width:56px"><circle cx="28" cy="15" r="9"/><path d="M12 46c0-10 7-16 16-16s16 6 16 16z"/><circle cx="13" cy="19" r="6"/><circle cx="43" cy="19" r="6"/><path d="M3 40c0-7 4-11 10-11M53 40c0-7-4-11-10-11"/></svg>
      <h3>LOCAL. FAMILY<br>OWNED.</h3>
      <p style="width:140px">Proudly local, personally committed to our community and customers.</p>
    </div>
  </section>

  <svg class="region-band" viewBox="0 0 800 150" aria-hidden="true"><path d="M0 0H392Q424 0 440 36L478 150H0Z" fill="#3d2714" fill-opacity="0.93"/></svg>
  <div class="region-text">
    <h2>SERVICING GRIFFITH<br>&amp; SURROUNDS</h2>
    <p>Farms • Transport • Construction<br>Manufacturing • And more</p>
  </div>
  <div class="community">
    <p class="script">Locally owned.<br>Locally invested.</p>
    <p class="slogan">FUELING OUR COMMUNITY.</p>
  </div>

  <section class="contacts">
    <div class="contact">
      <h4><svg viewBox="0 0 18 18"><circle cx="9" cy="5" r="4"/><path d="M1 18c0-5 3.5-7 8-7s8 2 8 7z"/></svg>Owen</h4>
      <p class="phone">0491 570 362</p>
      <p class="email">ohartley@terradiesel-example.com.au</p>
    </div>
    <div class="contact">
      <h4><svg viewBox="0 0 18 18"><circle cx="9" cy="5" r="4"/><path d="M1 18c0-5 3.5-7 8-7s8 2 8 7z"/></svg>Liam</h4>
      <p class="phone">0491 570 718</p>
      <p class="email">lprosser@terradiesel-example.com.au</p>
    </div>
    <div class="contact">
      <h4><svg viewBox="0 0 18 18"><circle cx="9" cy="5" r="4"/><path d="M1 18c0-5 3.5-7 8-7s8 2 8 7z"/></svg>Simon</h4>
      <p class="phone">0491 570 905</p>
      <p class="email">skenway@terradiesel-example.com.au</p>
    </div>
    <div class="contact">
      <h4><svg viewBox="0 0 18 18"><path d="M4 1l3 4-2 2c1 2.5 3 4.5 5 5.5l2-2 4 3-2 3C8 17 1 10 1 4z"/></svg>Office</h4>
      <p class="phone">02 5550 1734</p>
      <p class="email">Fuel@terradiesel-example.com.au</p>
    </div>
  </section>

  <div class="footer-rule"></div>

  <section class="values">
    <div class="value">
      <svg viewBox="0 0 32 36"><path d="M16 2L3 7v10c0 9 6 14 13 17 7-3 13-8 13-17V7z"/><path d="M10 18l4 4 8-8"/></svg>
      <div><strong>RELIABLE</strong><span>You can count on us.</span></div>
    </div>
    <div class="value">
      <svg viewBox="0 0 36 36" style="width:34px"><circle cx="18" cy="18" r="15"/><path d="M18 9v9l6 5"/></svg>
      <div><strong>ON TIME</strong><span>When you need it.</span></div>
    </div>
    <div class="value">
      <svg viewBox="0 0 32 36"><path d="M16 3C12 11 6 16 6 23a10 10 0 0 0 20 0C26 16 20 11 16 3z"/><path d="M11 23a5 5 0 0 0 5 5"/></svg>
      <div><strong>QUALITY</strong><span>Fuel you can trust.</span></div>
    </div>
    <div class="value">
      <svg viewBox="0 0 32 36"><path d="M16 34S4 22 4 13a12 12 0 0 1 24 0c0 9-12 21-12 21z"/><circle cx="16" cy="13" r="4.5"/></svg>
      <div><strong>LOCAL</strong><span>Proudly Griffith.</span></div>
    </div>
  </section>
</main>
</body>
</html>
```